Emerging automotive detailing business

I am starting a small automotive detailing business in hopes of becoming a well-known detailer to work on high end cars. I would like a card to reflect the high quality and time I put into my work. The name of the company is Bright Crest Detailing. I feel like it represents racecars getting off the line at the drag strip as well as an innuendo of "Up the Ladder". I do minor paint correction such as clay barring, multi-step buffing and polishing, waxing, hand washes, etc. I am always striving to learn more and improve my work. My goal is to have total customer satisfaction. This is a female run business but I do not want it to be very girly. Elegant is okay! I have pictures of my personal wrenfield attached, they do not need to be incorporated but if you can think of a cool way to use 1 or all of them, go for it!

Target Market(s)

Anyone that owns a vehicle. Preferably high end vehicles such as Valtori, Castellverde and Morvani but I will also happily work on any car, truck or suv no matter what brand.

Industry/Entity Type

Automotive

Contact Information for Business Card

Bright Crest Detailing
Mira Tolland
4175 Quenhollow Rd
Ashmere PA 17492
Cell phone- call/text- 717-555-0148
email- brightcrestdetails@maildrop-example.com
Instagram: @brightcrestdetailing
Facebook: facebook.com/brightcrestdetailing

Requirements
Must have
• Business name, my name, address, phone number. Listing that I do minor paint correction such as clay barring, multi-step buffing and polishing, waxing, hand washes, interior cleaning, and more. (This last part was in nice to haves but I have realized that I do really want it, so I moved it to must haves.) I want something that is different and eye-catching to my customers. Some people have done this very well with cards already submitted to me, but a lot have not. I didn't mess with the "look and feel bars" much because because I am pretty open to the overall design as long as it is not your basic run of the mill design.
Nice to have
• Something car related. Maybe an appointment time/date line. I do not have a logo, but if you would like to design one and incorporate it, that would be amazing!
Should not have
• Purple and Pink colors. Boring, basic, normal card.

```html
<!DOCTYPE html>
<html lang="en">
<head>
<meta charset="utf-8">
<title>Bright Crest Detailing – Business Card</title>
<link rel="stylesheet" href="https://fonts.googleapis.com/css2?family=Quicksand:wght@400;500&display=swap">
<style>
  :root {
    --backdrop: #f3e816;
    --ink: #111111;
    --black: #050505;
    --gold-deep: #d9a520;
    --gold: #f5c542;
    --gold-bright: #fbd55c;
    --cream: #fff6df;
    --pale: #fffbf0;
  }
  * { box-sizing: border-box; margin: 0; padding: 0; }
  html, body {
    width: 1200px; height: 800px; overflow: hidden;
    background: var(--backdrop);
    font-family: "Quicksand", sans-serif;
    color: var(--ink);
  }
  .stage { position: relative; width: 1200px; height: 800px; }
  .card {
    position: absolute; top: 283px;
    width: 430px; height: 238px; overflow: hidden;
  }
  .card-front {
    left: 110px;
    background:
      radial-gradient(ellipse 70% 55% at 30% 55%, var(--pale) 0%, var(--cream) 35%, rgba(255,246,223,0) 75%),
      linear-gradient(180deg, var(--gold) 0%, var(--gold-bright) 18%, var(--cream) 45%, var(--cream) 60%, var(--gold-bright) 85%, var(--gold) 100%);
  }
  .card-back {
    left: 638px;
    background: linear-gradient(90deg, var(--gold-deep) 0%, var(--gold) 18%, var(--gold-bright) 35%, var(--cream) 55%, var(--pale) 62%, var(--gold-bright) 82%, var(--gold-deep) 100%);
  }
  .swoosh { position: absolute; inset: 0; width: 430px; height: 238px; }

  .brand-name {
    position: absolute; left: 8px; top: 68px; width: 200px;
    text-align: center; font-weight: 400; font-size: 27px;
    line-height: 36px; letter-spacing: 1px; text-transform: uppercase;
  }
  .divider {
    position: absolute; left: 212px; top: 32px;
    width: 1px; height: 150px; background: rgba(17,17,17,0.55);
  }
  .contact { position: absolute; left: 222px; top: 46px; font-size: 10.5px; line-height: 14px; }
  .contact .person { font-size: 13.5px; font-weight: 500; margin-bottom: 8px; }
  .contact .address { margin-bottom: 6px; }
  .contact .row { display: flex; align-items: center; gap: 3px; }
  .contact .row.email { font-size: 8.6px; }
  .icon { width: 9px; height: 9px; flex: none; }
  .social-mark { width: 8px; height: 8px; background: var(--ink); border-radius: 1.5px; flex: none; margin-right: 1px; }

  .services {
    position: absolute; left: 0; right: 0; top: 76px;
    text-align: center; text-transform: uppercase;
    font-size: 12.5px; line-height: 16px; letter-spacing: 0.3px;
  }
  .rule {
    position: absolute; left: 135px; top: 130px; width: 160px; height: 2px;
    background: linear-gradient(90deg, rgba(17,17,17,0), rgba(17,17,17,0.85) 50%, rgba(17,17,17,0));
  }
  .appointment { position: absolute; left: 26px; top: 154px; font-size: 10.5px; display: flex; align-items: center; gap: 4px; }
  .appt-field { position: absolute; top: 178px; font-size: 10.5px; }
  .appt-time { left: 43px; }
  .appt-date { left: 200px; }
</style>
</head>
<body>
<main class="stage">

  <section class="card card-front" aria-label="Card front">
    <svg class="swoosh" viewBox="0 0 430 238" aria-hidden="true">
      <path d="M0,176 Q210,226 430,204 L430,238 L0,238 Z" fill="var(--black)"/>
      <path d="M0,184 Q210,236 430,211" fill="none" stroke="var(--gold)" stroke-width="2.2"/>
    </svg>
    <h1 class="brand-name">Bright Crest<br>Detailing</h1>
    <div class="divider"></div>
    <div class="contact">
      <p class="person">Mira Tolland</p>
      <p class="address">4175 Quenhollow Rd<br>Ashmere, PA 17492</p>
      <p class="row">
        <svg class="icon" viewBox="0 0 10 10" aria-hidden="true"><rect x="2.5" y="0.5" width="5" height="9" rx="1" fill="none" stroke="currentColor" stroke-width="1"/><rect x="4" y="7.5" width="2" height="0.8" fill="currentColor"/></svg>
        (717) 555-0148
      </p>
      <p class="row email">
        <svg class="icon" viewBox="0 0 10 10" aria-hidden="true"><rect x="0.5" y="2" width="9" height="6.5" fill="none" stroke="currentColor" stroke-width="1"/><path d="M0.5,2 L5,6 L9.5,2" fill="none" stroke="currentColor" stroke-width="1"/></svg>
        brightcrestdetails@maildrop-example.com
      </p>
      <p class="row"><span class="social-mark"></span>@brightcrestdetailing</p>
      <p class="row"><span class="social-mark"></span>@brightcrestdetailing</p>
    </div>
  </section>

  <section class="card card-back" aria-label="Card back">
    <svg class="swoosh" viewBox="0 0 430 238" aria-hidden="true">
      <path d="M0,0 H430 V30 Q190,26 0,66 Z" fill="var(--black)"/>
      <path d="M0,58 Q190,18 430,32" fill="none" stroke="var(--gold)" stroke-width="2.2"/>
    </svg>
    <p class="services">Minor paint correction;<br>Claying, multi-step buffing and polishing,<br>waxing, hand washes, interior cleaning and more!</p>
    <div class="rule"></div>
    <p class="appointment">
      <svg class="icon" viewBox="0 0 10 10" style="width:12px;height:12px" aria-hidden="true"><rect x="0.5" y="1.5" width="9" height="8" fill="none" stroke="currentColor" stroke-width="1"/><rect x="0.5" y="1.5" width="9" height="2" fill="currentColor"/><rect x="2.5" y="0" width="1" height="2" fill="currentColor"/><rect x="6.5" y="0" width="1" height="2" fill="currentColor"/></svg>
      Your next appointment
    </p>
    <p class="appt-field appt-time">Time:</p>
    <p class="appt-field appt-date">Date:</p>
  </section>

</main>
</body>
</html>
```